Celvara Health Group Presentation Folder, for Cancer Awareness, VERY COLORFUL AND MODERN

Presentation Folder I know pretty much what i want so it should be very eazy , I have included files from folders I use now rebrand them to my new company they will be fine, no sense re creating the wheel
Full Bleed Size
20.87" x 16.68"
53 x 42.4 cm
6260 x 5004 pixels
Document Trim Size
20.75" x 16.56"
52.7 x 42.1 cm
6225 x 4969 pixels

Low design quality

Industry/Entity Type

Medical

Font styles to use
Serif

Colors

Designer to choose colors to be used in the design.

Requirements
Must have
• really I am not looking for some one to redesign, we like our folder front page and would like to see new word information added., there are two folder front pages to choose from
• So Keep the original front page and redesign the back page and the pockets
• Can Make your Design off of one of the ones I already uploaded
Nice to have
• Keep the same color schemes, Keep the original front page and redesign the back page and the pockets
Should not have
• DO not recreate the front covers, use what I gave you and just rebrand

```html
<!DOCTYPE html>
<html lang="en">
<head>
<meta charset="utf-8">
<title>Celvara Health Group – Presentation Folder</title>
<link href="https://fonts.googleapis.com/css2?family=Oswald:wght@500&family=PT+Sans:wght@400;700&family=Roboto+Condensed:wght@400&display=swap" rel="stylesheet">
<style>
  :root{
    --navy:#1c2f5e;
    --navy-deep:#15264f;
    --green:#96c24b;
    --white:#ffffff;
    --stage:#858585;
    --ink:#1a1a1a;
    --photo-sky:#8ea4b8;
    --photo-ground:#6f6a5e;
  }
  html,body{margin:0;padding:0;overflow:hidden;}
  body{width:1200px;height:1200px;background:var(--stage);position:relative;font-family:"PT Sans",sans-serif;}
  .folder-art{position:absolute;left:0;top:0;width:1200px;height:1200px;}
  .abs{position:absolute;margin:0;}
  .back-intro{left:179px;top:100px;width:276px;color:var(--white);font-size:9.2px;line-height:12.3px;text-align:justify;}
  .back-quote{left:179px;top:188px;width:300px;color:var(--white);font-size:13px;line-height:16.5px;}
  .contact-list{left:190px;top:399px;list-style:none;padding:0;color:var(--white);font-size:9px;}
  .contact-list li{display:flex;align-items:center;height:19px;padding-left:20px;}
  .contact-list li:last-child{margin-top:2px;}
  .cover-brand{left:595px;top:102px;width:340px;text-align:center;color:var(--navy);font-size:12px;font-weight:700;}
  .cover-title{left:595px;top:172px;width:340px;text-align:center;color:var(--navy);font-family:"Oswald",sans-serif;font-weight:500;font-size:25px;letter-spacing:-0.3px;line-height:32px;}
  .cover-subtitle{left:595px;top:208px;width:340px;text-align:center;color:var(--navy);font-family:"Oswald",sans-serif;font-weight:500;font-size:14.5px;line-height:18px;letter-spacing:-0.3px;}
  .cover-lead{left:595px;top:238px;width:340px;text-align:center;color:var(--navy);font-size:9px;font-weight:700;line-height:12.4px;}
  .cover-url{left:595px;top:522px;width:340px;text-align:center;color:var(--white);font-size:12px;letter-spacing:3px;}
  .inside-copy{left:667px;top:689px;width:321px;color:var(--ink);font-size:9.4px;line-height:12.4px;text-align:justify;}
  .inside-copy p{margin:0 0 16px;}
  .inside-heading{left:667px;top:874px;width:330px;color:var(--ink);font-family:"Roboto Condensed",sans-serif;font-size:16.5px;line-height:21px;}
  .pocket-brand{left:322px;top:1028px;display:flex;align-items:center;gap:10px;color:var(--white);}
  .pocket-brand .mark{width:52px;height:52px;border:2px solid var(--white);border-radius:50%;box-sizing:border-box;}
  .pocket-brand .name{font-size:17px;line-height:19px;letter-spacing:1.5px;text-transform:uppercase;}
  .card-label{left:776px;top:1020px;width:150px;text-align:center;color:var(--ink);font-size:13px;line-height:18px;}
</style>
</head>
<body>

<svg class="folder-art" viewBox="0 0 1200 1200" xmlns="http://www.w3.org/2000/svg">
  <defs>
    <linearGradient id="fold-shade" x1="0" x2="1" y1="0" y2="0">
      <stop offset="0" stop-color="#ffffff"/>
      <stop offset="0.7" stop-color="#ececec"/>
      <stop offset="1" stop-color="#bdbdbd"/>
    </linearGradient>
    <linearGradient id="photo-tone" x1="0" x2="0" y1="0" y2="1">
      <stop offset="0" stop-color="var(--photo-sky)"/>
      <stop offset="0.55" stop-color="#a3a9aa"/>
      <stop offset="1" stop-color="var(--photo-ground)"/>
    </linearGradient>
    <linearGradient id="ribbon-tone" x1="0" x2="1" y1="0" y2="0">
      <stop offset="0" stop-color="#3dbbe8"/>
      <stop offset="1" stop-color="#a985c4"/>
    </linearGradient>
    <linearGradient id="pocket-tone" x1="0" x2="1" y1="0" y2="0">
      <stop offset="0" stop-color="var(--navy-deep)"/>
      <stop offset="0.5" stop-color="#27407a"/>
      <stop offset="1" stop-color="var(--navy-deep)"/>
    </linearGradient>
  </defs>

  <g class="outer-spread">
    <rect x="158" y="77" width="783" height="496" fill="var(--navy)"/>
    <path class="cover-white" d="M600 77 H941 V300 C870 290 800 315 700 305 C560 230 550 160 600 77 Z" fill="var(--white)"/>
    <path class="top-swoosh" d="M488 77 H600 C550 160 560 230 700 305 C620 300 550 290 520 240 C490 190 480 130 488 77 Z" fill="var(--green)"/>
    <path d="M600 77 C550 160 560 230 700 305" fill="none" stroke="var(--white)" stroke-width="1.5"/>
    <path class="cover-photo" role="img" aria-label="Photo: family of three generations holding hands on a beach, seen from behind"
          d="M550 300 C650 290 720 322 800 312 C860 305 900 300 941 312 V462 C880 468 820 458 760 464 C660 474 600 480 550 470 Z"
          fill="url(#photo-tone)"/>
    <path class="bottom-swoosh" d="M158 462 C260 515 360 540 450 538 C540 536 620 502 941 480 V490 C700 505 610 512 560 525 C500 545 470 552 440 552 C340 553 240 540 158 505 Z" fill="var(--green)"/>
    <path d="M158 462 C260 515 360 540 450 538 C540 536 620 502 941 480" fill="none" stroke="var(--white)" stroke-width="1.5"/>
    <line x1="550" y1="77" x2="550" y2="573" stroke="#000" stroke-opacity="0.08"/>
  </g>

  <g class="inside-spread">
    <rect x="237" y="630" width="790" height="500" fill="var(--white)"/>
    <rect x="455" y="630" width="177" height="500" fill="url(#fold-shade)"/>
    <line x1="455" y1="630" x2="455" y2="964" stroke="#e2e2e2"/>
    <rect class="awareness-ribbon" role="img" aria-label="Blue and purple awareness ribbon" x="374" y="742" width="124" height="172" rx="10" fill="url(#ribbon-tone)"/>
    <path class="pocket-left" d="M237 964 H600 Q610 964 612 975 L632 1130 H237 Z" fill="url(#pocket-tone)"/>
    <path class="pocket-right" d="M1027 964 H670 Q658 964 655 975 L632 1130 H1027 Z" fill="url(#pocket-tone)"/>
    <g class="card-slot">
      <rect x="776" y="990" width="150" height="104" fill="var(--white)"/>
      <path d="M776 998 L790 990 M912 990 L926 998 M776 1086 L790 1094 M912 1094 L926 1086" stroke="var(--navy-deep)" stroke-width="3"/>
    </g>
  </g>

  <g class="contact-icons" fill="var(--green)">
    <path d="M193 403 l3 -1 l2 3 l-1.5 1.2 a7 7 0 0 0 3.3 3.3 l1.2 -1.5 l3 2 l-1 3 a10 10 0 0 1 -10 -10 z"/>
    <path d="M193 422 l3 -1 l2 3 l-1.5 1.2 a7 7 0 0 0 3.3 3.3 l1.2 -1.5 l3 2 l-1 3 a10 10 0 0 1 -10 -10 z"/>
    <circle cx="197" cy="445" r="5" fill="none" stroke="var(--green)" stroke-width="1.2"/>
    <path d="M192 445 H202 M197 440 V450" stroke="var(--green)" stroke-width="0.9"/>
  </g>
</svg>

<p class="abs back-intro">Hereditary cancer screening provides vital information to help people with a strong personal or family history of cancer understand their own risk of developing the disease. With this information, they can take steps to Potentially Prevent Cancer, Delay the Onset of Cancer or Catch it at an Earlier stage when outcomes and survival rates are Better.</p>
<p class="abs back-quote">Knowledge is Power and Power Eradicates Fear. When You are Fearless, You Will Make all the Right Choices!</p>
<ul class="abs contact-list">
  <li>555-0142-318</li>
  <li>555-0142-319</li>
  <li>hello@celvarahealth.com</li>
</ul>

<p class="abs cover-brand">Celvara Health Group</p>
<h1 class="abs cover-title">HEREDITARY CANCER SCREENING</h1>
<h2 class="abs cover-subtitle">DOCTORS ARE THE GATEKEEPERS TO GENETIC TESTING.</h2>
<p class="abs cover-lead">We have an obligation to help patients understand genetic risk<br>and how testing can guide heath care decisions.</p>
<p class="abs cover-url">www.celvarahealth.com</p>

<div class="abs inside-copy">
  <p>There are many benefits to getting tested, regardless of the eventual result. If one of your family members — however distant — had cancer, there is a chance that you inherited a gene mutation that not only increases your personal risk of cancer, but also could be passed to the next generation. Those who are carriers of hereditary cancer gene mutations, could be at risk of getting cancer earlier in life than the general population. The sooner genetic testing is done, the more likely it is that the risk can be managed appropriately.</p>
  <p>Hereditary cancer screening provides vital information to help people with a strong personal or family history of cancer understand their own risk of developing the disease. With this information, they can take steps to Potentially Prevent Cancer, Delay the Onset of Cancer or Catch it at an Earlier stage when outcomes and survival rates are Better.</p>
</div>
<p class="abs inside-heading">Identifying an inherited genetic mutation has the potential to prevent cancer and save lives.</p>

<div class="abs pocket-brand">
  <span class="mark"></span>
  <span class="name">Celvara<br>Health<br>Group</span>
</div>
<p class="abs card-label">Space for<br>Business card</p>

</body>
</html>
```